SaaS Early tech startup business card design

Unique design for experience ecommerce platform company. the business cards will be used by executive members. conformance with color code is required.

```html
<!DOCTYPE html>
<html lang="en">
<head>
<meta charset="utf-8">
<title>Kivo business card</title>
<link rel="stylesheet" href="https://fonts.googleapis.com/css2?family=Montserrat:wght@400;500&family=Roboto:wght@400;700&display=swap">
<style>
  :root {
    --backdrop: #6b6868;
    --card-dark: #1f2137;
    --card-light: #f2f2f2;
    --brand-teal: #1aa79a;
    --name-teal: #17606a;
    --ink: #2b2b2b;
    --white: #ffffff;
  }
  * { box-sizing: border-box; margin: 0; padding: 0; }
  html, body { width: 1200px; height: 1200px; overflow: hidden; }
  body {
    background: var(--backdrop);
    font-family: "Roboto", Arial, sans-serif;
    position: relative;
  }
  .card {
    position: absolute;
    width: 593px;
    height: 348px;
    border-radius: 24px;
    overflow: hidden;
  }
  .card--front { left: 300px; top: 198px; background: var(--card-dark); }
  .card--back  { left: 292px; top: 637px; background: var(--card-light); }

  .wordmark {
    font-family: "Roboto", Arial, sans-serif;
    font-weight: 700;
    color: var(--brand-teal);
    line-height: 1;
    letter-spacing: 0.01em;
  }
  .tagline {
    font-family: "Montserrat", Arial, sans-serif;
    font-weight: 400;
    text-transform: uppercase;
    white-space: nowrap;
  }

  .front-brand {
    position: absolute;
    left: 0; right: 0; top: 114px;
    text-align: center;
  }
  .front-brand .wordmark { font-size: 92px; }
  .front-brand .tagline {
    margin-top: 6px;
    color: var(--white);
    font-size: 15.5px;
    letter-spacing: 0.36em;
    padding-left: 0.36em;
  }

  .corner-accent {
    position: absolute;
    right: 8px; bottom: 8px;
    width: 104px; height: 104px;
    border-radius: 50%;
    border: 2px solid var(--brand-teal);
    opacity: 0.5;
  }
  .card--back .corner-accent { opacity: 0.3; }

  .contact-block {
    position: absolute;
    left: 65px; top: 78px;
    color: var(--ink);
  }
  .contact-block .person-name {
    font-weight: 700;
    font-size: 23px;
    color: var(--name-teal);
    letter-spacing: -0.01em;
  }
  .contact-block .person-role {
    font-size: 15px;
    margin-top: 2px;
  }
  .contact-list {
    list-style: none;
    margin-top: 26px;
    font-size: 15.5px;
  }
  .contact-list li {
    display: flex;
    align-items: center;
    height: 22.5px;
  }
  .contact-icon {
    width: 14px; height: 14px;
    margin-right: 16px;
    flex: none;
  }
  .contact-icon--solid { fill: var(--name-teal); }
  .contact-icon--line { fill: none; stroke: var(--name-teal); stroke-width: 1.4; }
  .address {
    margin-top: 6px;
    font-size: 15.5px;
    line-height: 22.5px;
  }

  .back-brand {
    position: absolute;
    left: 280px; top: 120px;
    width: 252px;
    text-align: center;
  }
  .back-brand .wordmark { font-size: 78px; }
  .back-brand .tagline {
    margin-top: 8px;
    color: var(--brand-teal);
    font-weight: 500;
    font-size: 12.5px;
    letter-spacing: 0.3em;
    padding-left: 0.3em;
  }
</style>
</head>
<body>

  <section class="card card--front" aria-label="Card front">
    <div class="front-brand">
      <div class="wordmark">kivo</div>
      <div class="tagline">Built around you</div>
    </div>
    <div class="corner-accent"></div>
  </section>

  <section class="card card--back" aria-label="Card back">
    <div class="contact-block">
      <div class="person-name">Rami T.</div>
      <div class="person-role">CTO/Owner</div>
      <ul class="contact-list">
        <li>
          <svg class="contact-icon contact-icon--solid" viewBox="0 0 16 16" aria-hidden="true"><path d="M1 6c0-2 3-3.5 7-3.5S15 4 15 6v1.2h-3.2V5.8H4.2v1.4H1z M3.5 8h9l1.5 6H2z"/></svg>
          (00) 0123 4567
        </li>
        <li>
          <svg class="contact-icon contact-icon--line" viewBox="0 0 16 16" aria-hidden="true"><rect x="1.5" y="3.5" width="13" height="9"/><path d="M1.5 3.5L8 9l6.5-5.5"/></svg>
          hello@kivo.io
        </li>
        <li>
          <svg class="contact-icon contact-icon--line" viewBox="0 0 16 16" aria-hidden="true"><circle cx="8" cy="8" r="6.3"/><ellipse cx="8" cy="8" rx="2.8" ry="6.3"/><path d="M1.7 8h12.6"/></svg>
          www.kivo.io
        </li>
      </ul>
      <div class="address">
        Harbor Tower, Dubai<br>
        Media Park District, UAE
      </div>
    </div>

    <div class="back-brand">
      <div class="wordmark">kivo</div>
      <div class="tagline">Built around you</div>
    </div>
    <div class="corner-accent"></div>
  </section>

</body>
</html>
```